SaaS / Consulting / Solution website redesign

We need a website design that:
- Is completely different than our current design : https://plumvessel.net
- Has a very minimal amount of copy
- Changes our positioning from a SaaS application to a solutions company. Solutions company means that we help our customers solve their problems with consulting, training, and tools. An example of a solutions company is here: https://oldpages.example/web/20130111103320/http://www.brindlework.com:80/
- Does not make us look like a start up
- Is more people oriented than technology oriented

We need a designer that:
- Is a rebel at heart
- Is a minimalist
- Tells us why our current site sucks
- Can disagree with us
- Can also do copywriting or already has a copywriter that can help
- Is ok with saying we have capability that we don't in order to see if people actually want that
- Can understand the difference between our grand vision and where we need to focus ourselves today in order to get there

Who we are:
- Entrepreneurs
- Programmers
- Consultants
- Investors

Here's our design goals:
#1 Get customers, investors, employers, and partners excited about our unique and clearly articulated value proposition
#2 Get people to contact us asking for help with their programs
#3 Position ourselves as an expert in the skills based volunteering, mentorship, and group collaboration
#4 Make it easy for people, who already know who we are, to register online

What our grand vision is:
- Create a marketplace where any person can go to our site and find time with anyone they need to meet with. Whether that is their hair stylist, school advisor, parent of your kids class, dentist, attorney, etc.

What will you get if you win:
- In addition to the prize of this project we will have many landing pages and other revisions we will need in the future. We currently don't have a designer or copywriter and need to add that capability to our team

Who do we need to appeal to:
- Directors that are launching innovative programs inside organizations
- IT personnel who are trying to disqualify our technology so they don't have to support it or deal with it when it doesn't go well
- Enterprise IT architects who don't want our product being on its own island within their organization totally incompatible with everything else. Architects which are trying to assess how our platform will co-exist with all their other platforms
- Vice Presidents who want to help their directors understand that we don't have enough experience to help them
- Program managers who have to juggle a million things and need a tool that actually helps instead of confuses them and adds more work for them.
- Program managers & directors that have been given ambiguous goals by their board of directors like "improve retention, increase engagement, create innovation, get people to collaborate." And who have no idea where to start or how to deliver on things like that.
- Program managers, directors, and vice presidents that are trying to understand how our technology and services fit into their existing technology and capability
- Employees who are bored and uninspired with their current tools and are hoping for some excitement in their life. Kind of like candy or a double espresso.
- Investors who think, our company like all the rest, are going to waste their money and make them look like a fool

Other information:
-The CSS and html needs to be responsive

-Our registration onboarding flow needs to collect this information:
User first name
user last name
user email
(verify their email)
user phone number
(verify their phone number)
User profile image (optional)
User profile summary (optional, like a bio, freeform text fiels)
If applicable: Register their organization
Organization name
Organization image (optional)
Account Mailing address
account Billing address (could be same as mailing address)
account Billing email address (could be same as user address)
account Product selection (pricing tier)
account Credit card information

The designs I am getting are a good start but they are only the front page. I just want you to know that I am expecting and need more than a landing page to complete the design. I will likely need a page that outlines the benefits and features of the product itself, how its different than our competitors, which will not be on the front page. I will need a registration flow. I will need a blog page design so we can post blog articles, I will need a team page, a page that goes into detail on our training, our services. I will likely need a page that shows all news and media we have been in. I need to show customer and user quotes, case studies, a way to contact us, partners, general resources like on collaboration, product tutorials, customers. I need the site to address a comprehensive set of needs. I need that design to be consistent and thorough. I know what PlateHarbor is. I'm not using because I need more than a template that was customized. I need to be unique and match our brand thoughtfully, beautifully, and artistically. Someone asked me a question about how Murmly is similar to our tool in the way it is referred by end users and purchased by managers. Our website needs to primarily talk to the managers as I explained in the brief but it needs to appear cool and exciting to our end-users without focusing on the technology too much. Murmly is a tool that teams use to collaborate in small and large enterprises. The value prop for them is that communication is easier. But they don't put that on their website. Why? Because the users of the technology won't go to the website to find out information on it, they get their information from someone who is using it and demos it to them. When Ines tells her manager Otto "Lets get murmly, Ruth is using it at her company and its great" Ines's manager doesn't know anything about murmly so she promptly googles it. The most important thing from Ines's perspective is that Otto agrees to try it out. Otto's biggest concern is that productivity will be enhanced to degraded. Murmly knows this and so on the front page they know they are talking to Otto NOT Ines because Ines is already sold on it and doesn't need to get sold on the website. Ines is end user. Otto is the purchaser. We have the same problem and so our end users are not the ones purchasing our product, their managers are purchasing our product. We get referred by our end users and vetted by their managers. Hope this helps! Thank you for looking at this project!  Added Wednesday, June 7, 2017

Another observation I am having about the designs being submitted. I believe we used the animations on our current website because animations / cartoons connect with the "inner child" in our users. Whatever that means :-). I think it's what makes our brand fun. I have a hard time imagining that we could make the design fun looking without animations but I'm sure it can be achieved. I also recognize that blending pictures of real people and animations is hard. So either we must masterfully blend them, use only animations, or make the real people have a LOT of fun! So far most of the designs while achieve the goal of appealing to the serious Vice Presidents and directors, they are not doing a good job at appealing to the overworked program managers and bored employees. There seems to stand another challenge with animations which is animations are hard to find and/or create that achieve the message / emotion we are trying to communicate. I don't have any good answers for this but I will say we can hire both animators and illustrators if we need to. All you have to do is communicate the effect in the website design with some simpler version maybe not the end illustration or animation itself. Added Wednesday, June 7, 2017

• Sex appeal and a sense of humor. Copy that makes people excited and clairvoyant about our potential.
• Boring renditions of other non-inspiring websites

```html
<!DOCTYPE html>
<html lang="en">
<head>
<meta charset="utf-8">
<title>Plumvessel — Register Now</title>
<link rel="stylesheet" href="https://fonts.googleapis.com/css2?family=Roboto:wght@300;400;500&display=swap">
<style>
  :root {
    --sky-top: #3d9de3;
    --sky-bottom: #2a86cd;
    --footer-band: #0f5a92;
    --card-bg: #ffffff;
    --field-border: #b4b4b4;
    --ink: #2b2b2b;
    --placeholder: #333333;
    --button-top: #2f86c6;
    --button-bottom: #0c5593;
    --on-blue: #ffffff;
  }
  * { box-sizing: border-box; margin: 0; padding: 0; }
  html, body { width: 1200px; height: 842px; overflow: hidden; }
  body { font-family: "Roboto", Arial, sans-serif; color: var(--ink); }

  .stage {
    position: relative;
    width: 1200px;
    height: 842px;
    overflow: hidden;
  }
  .backdrop {
    position: absolute;
    inset: 0;
    background: linear-gradient(180deg, var(--sky-top) 0%, var(--sky-bottom) 100%);
  }
  .bottom-band {
    position: absolute;
    left: 0; right: 0; bottom: 0;
    height: 4px;
    background: var(--footer-band);
  }

  .brand {
    position: absolute;
    top: 34px;
    left: 0; right: 0;
    display: flex;
    justify-content: center;
    align-items: center;
    gap: 8px;
    color: var(--on-blue);
  }
  .brand-dot {
    width: 42px; height: 42px;
    border: 3px solid var(--on-blue);
    border-radius: 50%;
  }
  .brand-name {
    font-size: 26px;
    font-weight: 500;
    line-height: 1;
    padding-top: 8px;
  }

  .register-card {
    position: absolute;
    top: 117px;
    left: 367px;
    width: 463px;
    height: 626px;
    background: var(--card-bg);
    border-radius: 8px;
    box-shadow: 2px 3px 4px rgba(0, 0, 0, 0.25);
  }
  .register-title {
    position: absolute;
    top: 38px;
    left: 0; right: 0;
    text-align: center;
    font-size: 38px;
    line-height: 1;
    font-weight: 300;
    letter-spacing: -0.4px;
    color: var(--ink);
  }
  .register-form .field {
    position: absolute;
    left: 33px;
    width: 404px;
    height: 46px;
    border: 1px solid var(--field-border);
    background: var(--card-bg);
    font-family: "Roboto", Arial, sans-serif;
    font-size: 13px;
    font-weight: 300;
    color: var(--ink);
    padding: 0 12px;
    outline: none;
  }
  .register-form .field::placeholder { color: var(--placeholder); opacity: 1; }
  .register-form textarea.field {
    height: 100px;
    padding-top: 16px;
    resize: none;
  }
  .field-first { top: 106px; }
  .field-last { top: 167px; }
  .field-email { top: 229px; }
  .field-phone { top: 290px; }
  .field-image { top: 352px; }
  .field-summary { top: 413px; }

  .subscribe-button {
    position: absolute;
    top: 542px;
    left: 133px;
    width: 204px;
    height: 51px;
    border: none;
    border-radius: 3px;
    background: linear-gradient(180deg, var(--button-top) 0%, var(--button-bottom) 100%);
    color: var(--on-blue);
    font-family: "Roboto", Arial, sans-serif;
    font-size: 17.5px;
    font-weight: 400;
    letter-spacing: 0.2px;
    cursor: pointer;
  }

  .site-footer {
    position: absolute;
    top: 778px;
    left: 0; right: 0;
    text-align: center;
    color: var(--on-blue);
    font-size: 12.5px;
    font-weight: 400;
    line-height: 21px;
  }
</style>
</head>
<body>
  <main class="stage">
    <div class="backdrop" role="img" aria-label="Blue background with a faint pattern of connected network dots and lines"></div>

    <header class="brand">
      <span class="brand-dot"></span>
      <span class="brand-name">Plumvessel</span>
    </header>

    <section class="register-card">
      <h1 class="register-title">REGISTER NOW</h1>
      <form class="register-form">
        <input class="field field-first" type="text" placeholder="First Name">
        <input class="field field-last" type="text" placeholder="Last Name">
        <input class="field field-email" type="email" placeholder="Email">
        <input class="field field-phone" type="tel" placeholder="Phone">
        <input class="field field-image" type="text" placeholder="Profile Image (Optional)">
        <textarea class="field field-summary" placeholder="Profile Summary (Optional)"></textarea>
        <button class="subscribe-button" type="button">SUBSCRIBE</button>
      </form>
    </section>

    <footer class="site-footer">
      <p>© 2017 Plumvessel Inc All rights reserved</p>
      <p>Plumvessel® is a registered trademark of Plumvessel Inc</p>
    </footer>

    <div class="bottom-band"></div>
  </main>
</body>
</html>
```